Refresh of far from plain IT company website

Our web site is starting to show it's age. You can see the existing site here: www.plumbwick.net. As a growing company we want to come across as a dynamic collection of IT experts.

We want to update the design so are open to any colour palette and look, but want to retain our current table logo. We use the logo on our business cards but with a white background - see the attached file, so you don't need to keep the brown or the green.

The design should consider the range of browsers that will be looking at the site - so please show how it will look on a wide screen laptop and a 768x1024 tablet.

We want to add some pages about our team and their skills, probably with photos of each person on the team.

This is an uncoded project - the PSD files of the design is required, not coding.
Updates

Thanks everyone for the submissions so far.  It's a holiday day in the UK today but we will get some feedback on the designs so far out to you.

Target Market(s)

Architects and other creative types looking for IT support

Industry/Entity Type

Business

Font styles to use
Serif
Sans Serif

Requirements
Must have
• Must look good on a laptop and an iPad.

```html
<!DOCTYPE html>
<html lang="en">
<head>
<meta charset="utf-8">
<title>plumbwick – Serious IT Support For Business</title>
<link href="https://fonts.googleapis.com/css2?family=Open+Sans:ital,wght@0,400;0,600;0,700;1,700&display=swap" rel="stylesheet">
<style>
:root{
  --plum:#9a0a52;
  --plum-dark:#7d0642;
  --gold:#d9a900;
  --ink:#333;
  --muted:#666;
  --line:#dcdcdc;
  --panel:#f1f1f1;
  --icon:#666;
}
*{margin:0;padding:0;box-sizing:border-box}
html,body{width:1026px;height:1200px;overflow:hidden}
body{position:relative;background:#fff;font-family:"Open Sans",sans-serif;color:var(--ink)}
.abs{position:absolute}
.top-rule{left:0;top:0;width:1026px;height:3px;background:var(--plum)}
.brand{left:195px;top:24px;display:flex;align-items:center;gap:14px}
.brand-mark{width:48px;height:40px;background:var(--gold)}
.brand-name{font-size:42px;font-weight:600;color:var(--plum);letter-spacing:-0.5px;line-height:1}
.call{right:190px;top:14px;font-size:14px;color:#555;letter-spacing:.3px}
.chat{left:726px;top:43px;width:110px;height:42px;border:1px solid #d5d5d5;border-radius:4px;background:linear-gradient(#fff,#eee)}
.chat-photo{left:3px;top:-6px;width:34px;height:46px;border-radius:17px 17px 4px 4px;background:linear-gradient(#c9b6a6,#8a7468)}
.chat-text{left:40px;top:7px;font-size:11.5px;font-weight:600;line-height:15px;text-align:center}
.chat-text .live{color:var(--plum)}
.chat-text .avail{color:var(--gold)}
.nav{left:195px;top:96px;width:641px;display:flex;justify-content:space-between;list-style:none;font-size:9.5px;letter-spacing:.3px}
.nav li{color:#555;padding:0 3px;position:relative}
.nav li.active{color:var(--plum);font-weight:700}
.nav li.active::after{content:"";position:absolute;left:0;right:-4px;top:18px;height:2px;background:var(--plum)}
.nav-sep{position:absolute;top:97px;width:1px;height:12px;background:#ccc}
.page-band{left:0;top:122px;width:1026px;height:328px;background:linear-gradient(#fff,#d9d9d9)}
.hero{left:195px;top:122px;width:641px;height:328px;background:linear-gradient(110deg,#5d6270 0%,#9aa0ad 45%,#c3c6cf 60%,#6b7180 100%)}
.hero-band{left:195px;top:352px;width:641px;height:32px;background:rgba(200,200,205,.55);border-top:1px solid rgba(255,255,255,.4);border-bottom:1px solid rgba(255,255,255,.4)}
.hero-title{left:195px;top:350px;width:641px;text-align:center;font-size:26px;font-style:italic;font-weight:400;color:#111;letter-spacing:-.3px}
.dots{left:480px;top:396px;display:flex;gap:6px}
.dots span{width:10px;height:10px;border-radius:50%;background:#c9c9c9}
.dots span.on{background:var(--plum);border:2px solid #fff}
.band-rule{left:0;top:449px;width:1026px;height:4px;background:var(--plum);border-bottom:1px solid #e9c3d6}
.service-row{left:0;top:453px;width:1026px;height:60px;background:linear-gradient(#f2f2f2,#fff)}
.service{position:absolute;top:422px;width:130px;margin-left:-65px;text-align:center}
.service svg{display:block;margin:0 auto}
.service p{margin-top:12px;font-size:10.5px;font-weight:600;color:#333}
h2.section{position:absolute;font-size:16px;font-style:italic;font-weight:700;color:var(--plum);letter-spacing:-.3px;text-transform:uppercase;border-bottom:1px solid var(--line);padding-bottom:4px}
.about-text{left:196px;top:562px;width:412px;font-size:10.5px;line-height:18px;color:#333}
.about-text p+p{margin-top:12px}
.read-more{left:540px;top:704px;font-size:10.5px;color:var(--gold)}
.team{left:636px;top:524px;width:192px;height:192px;border-radius:50%;border:3px solid var(--plum);overflow:hidden;box-shadow:0 6px 8px rgba(0,0,0,.15)}
.team-photo{left:0;top:0;width:186px;height:130px;background:linear-gradient(#f3f3f3,#c9d6e6 60%,#3b3d45)}
.team-label{left:0;top:130px;width:186px;height:60px;background:var(--plum);color:#fff;text-align:center;font-size:21px;font-weight:600;padding-top:8px}
.card{position:absolute;top:786px;height:224px;border:2px solid #e0e0e0;background:var(--panel);box-shadow:0 8px 8px -4px rgba(0,0,0,.25)}
.avatar{position:absolute;width:60px;height:60px;border-radius:50%;border:3px solid #fff;background:linear-gradient(#d8d2cc,#6d6560);box-shadow:0 1px 3px rgba(0,0,0,.3)}
.who{position:absolute;width:110px;text-align:center}
.who b{display:block;font-size:12px;font-weight:600;color:#333}
.who span{font-size:9px;color:#777}
.quote{position:absolute;left:126px;width:172px;font-size:9.2px;line-height:12.5px;color:#444}
.qmark{position:absolute;font-size:22px;font-weight:700;color:#999;font-family:Georgia,serif;line-height:1}
.vline{position:absolute;left:96px;width:1px;background:#ddd}
.news-item{position:absolute;left:0;width:300px;height:74px}
.news-item svg{position:absolute;left:22px;top:10px}
.news-date{position:absolute;left:68px;top:6px;font-size:9.5px;font-weight:600;color:var(--plum)}
.news-text{position:absolute;left:68px;top:22px;width:210px;font-size:9.5px;line-height:13.5px;color:#444}
.news-div{position:absolute;left:20px;width:270px;height:1px;background:#ddd}
.pager{position:absolute;top:1016px;display:flex;gap:7px}
.footer{left:0;top:1044px;width:1026px;height:126px;background:var(--plum);color:#fff}
.footer h3{position:absolute;top:24px;font-size:13px;font-weight:400}
.links{position:absolute;top:50px;list-style:none;font-size:8.5px;line-height:18px}
.links li::before{content:"›";color:var(--gold);margin:0 9px 0 -12px;font-size:10px}
.fdiv{position:absolute;top:48px;width:1px;height:72px;background:rgba(255,255,255,.2)}
.news-sign{position:absolute;left:426px;top:48px;width:150px;font-size:9px;line-height:11.5px}
.email-field{position:absolute;left:426px;top:72px;width:112px;height:16px;background:#fff;border-radius:2px;color:#999;font-size:7.5px;padding:3px 5px}
.submit{position:absolute;left:425px;top:93px;width:53px;height:17px;border:1px solid var(--gold);border-radius:3px;font-size:9px;font-weight:700;text-align:center;line-height:15px}
.map{position:absolute;left:630px;top:47px;width:80px;height:62px;background:linear-gradient(135deg,#dcdcd4,#c8cfc2);border:1px solid #fff}
.contact{position:absolute;left:742px;font-size:8.5px;line-height:11px}
.contact-ico{position:absolute;left:724px}
.copy-bar{left:0;top:1170px;width:1026px;height:30px;background:var(--gold)}
.copy{left:195px;top:1177px;font-size:10px;color:#fff}
.social{position:absolute;top:1174px;width:21px;height:21px;border-radius:50%;background:#fff;border:2px solid #e6e6e6}
</style>
</head>
<body>
<div class="abs top-rule"></div>

<header>
  <div class="abs brand">
    <span class="brand-mark"></span>
    <span class="brand-name">plumbwick</span>
  </div>
  <div class="abs call">CALL US: 020 7000 4812</div>
  <div class="abs chat">
    <div class="abs chat-photo" role="img" aria-label="Support agent with headset"></div>
    <div class="abs chat-text"><div class="live">LIVE CHATT</div><div class="avail">AVAILABLE</div></div>
  </div>
  <ul class="abs nav">
    <li class="active">HOME</li><li>ABOUT US</li><li>WHAT WE DO</li><li>NEWS BLOG</li><li>ARTICLES</li><li>CLIENTS</li><li>PARTNERS</li><li>CONTACT US</li>
  </ul>
  <span class="nav-sep" style="left:246px"></span>
  <span class="nav-sep" style="left:329px"></span>
  <span class="nav-sep" style="left:427px"></span>
  <span class="nav-sep" style="left:519px"></span>
  <span class="nav-sep" style="left:598px"></span>
  <span class="nav-sep" style="left:673px"></span>
  <span class="nav-sep" style="left:758px"></span>
</header>

<section class="hero-area">
  <div class="abs page-band"></div>
  <div class="abs hero" role="img" aria-label="Businessman touching a glowing network of people icons"></div>
  <div class="abs hero-band"></div>
  <div class="abs hero-title">Serious It Support For Business</div>
  <div class="abs dots"><span class="on"></span><span></span><span></span><span></span></div>
  <div class="abs band-rule"></div>
  <div class="abs service-row"></div>

  <div class="service" style="left:257px">
    <svg width="54" height="54" viewBox="0 0 54 54"><circle cx="27" cy="27" r="25" fill="#fff" stroke="#ddd"/><circle cx="27" cy="27" r="22" fill="var(--icon)"/><path d="M18 36l10-10" stroke="#fff" stroke-width="4" stroke-linecap="round"/><circle cx="31" cy="22" r="6" fill="#fff"/><circle cx="34" cy="19" r="3" fill="var(--icon)"/></svg>
    <p>It Support &amp; Management</p>
  </div>
  <div class="service" style="left:387px">
    <svg width="54" height="54" viewBox="0 0 54 54"><circle cx="27" cy="27" r="25" fill="#fff" stroke="#ddd"/><circle cx="27" cy="27" r="22" fill="var(--icon)"/><path d="M17 33a5 5 0 010-10 7 7 0 0113-3 6 6 0 017 6 4 4 0 010 7z" fill="none" stroke="#fff" stroke-width="2.5"/></svg>
    <p>Cloud Computing</p>
  </div>
  <div class="service" style="left:515px">
    <svg width="54" height="54" viewBox="0 0 54 54"><circle cx="27" cy="27" r="25" fill="#fff" stroke="var(--gold)" stroke-width="2"/><circle cx="27" cy="27" r="22" fill="var(--plum)"/><rect x="22" y="21" width="10" height="17" rx="1" fill="#fff"/><path d="M27 11c3 4 5 6 3 9h-6c-2-3 0-5 3-9z" fill="#fff"/></svg>
    <p>Disaster Recovery</p>
  </div>
  <div class="service" style="left:646px">
    <svg width="54" height="54" viewBox="0 0 54 54"><circle cx="27" cy="27" r="25" fill="#fff" stroke="#ddd"/><circle cx="27" cy="27" r="22" fill="var(--icon)"/><rect x="22" y="14" width="10" height="19" rx="1" fill="#fff"/><path d="M27 33v5M19 39h16" stroke="#fff" stroke-width="2"/></svg>
    <p>Virtualisation</p>
  </div>
  <div class="service" style="left:769px">
    <svg width="54" height="54" viewBox="0 0 54 54"><circle cx="27" cy="27" r="25" fill="#fff" stroke="#ddd"/><circle cx="27" cy="27" r="22" fill="var(--icon)"/><path d="M27 14L16 37M27 14l11 23M19 30h16" stroke="#fff" stroke-width="3" stroke-linecap="round" fill="none"/></svg>
    <p>CAD Services</p>
  </div>
</section>

<section class="about">
  <h2 class="section" style="left:196px;top:528px;width:412px">About Us</h2>
  <div class="abs about-text">
    <p>Lorem ipsum dolor sit amet, consectetuer adipiscing elit, sed diam nonummy nibh euismod tincidunt ut laoreet dolore magna aliquam erat volutpat. Ut wisi enim ad minim veniam, quis nostrud exerci tation ullamcorper suscipit lobortis nisl ut aliquip ex ea comsed diam nonummy nibh euism od tincidunt ut laoreet dolore magna aliquam erat volutpat.</p>
    <p>Lorem ipsum dolor sit amet, consectetuer adipiscing elit, sed diam nonummy nibh euism od tincidunt ut laoreet dolore magna aliquam erat volutpat. Ut wisi enim ad minim venia m, quis nostrud....</p>
  </div>
  <div class="abs read-more">READ MORE...</div>
  <div class="abs team">
    <div class="abs team-photo" role="img" aria-label="Group photo of the team"></div>
    <div class="abs team-label">OUR TEAM</div>
  </div>
</section>

<section class="testimonials">
  <h2 class="section" style="left:197px;top:751px;width:306px">Testimonials</h2>
  <div class="card" style="left:196px;width:307px">
    <div class="avatar" style="left:20px;top:10px" role="img" aria-label="Client portrait"></div>
    <div class="who" style="left:-7px;top:75px"><b>Daniel Orrell</b><span>Businessman</span></div>
    <div class="vline" style="top:14px;height:88px"></div>
    <div class="qmark" style="left:108px;top:14px">“</div>
    <p class="quote" style="top:26px">Lorem ipsum dolor sit amet, consectetuer adipiscing elit, sed diam nonummyol nibh euismod tincidunt ut laoreet dolore magnarpl aliquam erat volutpat. Ut wisi enim adm minim.</p>
    <div class="qmark" style="left:158px;top:86px">”</div>
    <div class="avatar" style="left:20px;top:120px" role="img" aria-label="Client portrait"></div>
    <div class="who" style="left:-7px;top:184px"><b>Daniel Orrell</b><span>Businessman</span></div>
    <div class="vline" style="top:124px;height:88px"></div>
    <div class="qmark" style="left:108px;top:124px">“</div>
    <p class="quote" style="top:136px">Lorem ipsum dolor sit amet, consectetuer adipiscing elit, sed diam nonummyol nibh euismod tincidunt ut laoreet dolore magnarpl aliquam erat volutpat. Ut wisi enim adm minim.</p>
    <div class="qmark" style="left:156px;top:196px">”</div>
  </div>
  <div class="pager" style="left:325px">
    <svg width="13" height="13" viewBox="0 0 13 13"><circle cx="6.5" cy="6.5" r="6" fill="none" stroke="#555"/><path d="M9 6.5H4M6 4.5l-2 2 2 2" stroke="#555" fill="none"/></svg>
    <svg width="13" height="13" viewBox="0 0 13 13"><circle cx="6.5" cy="6.5" r="6" fill="none" stroke="#555"/><path d="M4 6.5h5M7 4.5l2 2-2 2" stroke="#555" fill="none"/></svg>
  </div>
</section>

<section class="news">
  <h2 class="section" style="left:530px;top:751px;width:307px">Latest News</h2>
  <div class="card" style="left:530px;width:307px">
    <div class="news-item" style="top:10px">
      <svg width="30" height="30" viewBox="0 0 30 30"><rect x="2" y="5" width="26" height="23" rx="2" fill="none" stroke="#666" stroke-width="2"/><path d="M2 11h26M9 2v6M21 2v6" stroke="#666" stroke-width="2"/><g fill="#666"><rect x="6" y="14" width="4" height="3"/><rect x="13" y="14" width="4" height="3"/><rect x="20" y="14" width="4" height="3"/><rect x="6" y="20" width="4" height="3"/><rect x="13" y="20" width="4" height="3"/><rect x="20" y="20" width="4" height="3"/></g></svg>
      <div class="news-date">12-APR-2014</div>
      <div class="news-text">Lorem ipsum dolor sit amet, consectetuer adipiscil ng elit, sed diam nonummy nibh...</div>
    </div>
    <div class="news-div" style="top:74px"></div>
    <div class="news-item" style="top:84px">
      <svg width="30" height="30" viewBox="0 0 30 30"><rect x="2" y="5" width="26" height="23" rx="2" fill="none" stroke="#666" stroke-width="2"/><path d="M2 11h26M9 2v6M21 2v6" stroke="#666" stroke-width="2"/><g fill="#666"><rect x="6" y="14" width="4" height="3"/><rect x="13" y="14" width="4" height="3"/><rect x="20" y="14" width="4" height="3"/><rect x="6" y="20" width="4" height="3"/><rect x="13" y="20" width="4" height="3"/><rect x="20" y="20" width="4" height="3"/></g></svg>
      <div class="news-date">15-APR-2014</div>
      <div class="news-text">Lorem ipsum dolor sit amet, consectetuer adipiscil ng elit, sed diam nonummy nibh...</div>
    </div>
    <div class="news-div" style="top:148px"></div>
    <div class="news-item" style="top:158px">
      <svg width="30" height="30" viewBox="0 0 30 30"><rect x="2" y="5" width="26" height="23" rx="2" fill="none" stroke="#666" stroke-width="2"/><path d="M2 11h26M9 2v6M21 2v6" stroke="#666" stroke-width="2"/><g fill="#666"><rect x="6" y="14" width="4" height="3"/><rect x="13" y="14" width="4" height="3"/><rect x="20" y="14" width="4" height="3"/><rect x="6" y="20" width="4" height="3"/><rect x="13" y="20" width="4" height="3"/><rect x="20" y="20" width="4" height="3"/></g></svg>
      <div class="news-date">17-APR-2014</div>
      <div class="news-text">Lorem ipsum dolor sit amet, consectetuer adipiscil ng elit, sed diam nonummy nibh...</div>
    </div>
  </div>
  <div class="pager" style="left:666px">
    <svg width="13" height="13" viewBox="0 0 13 13"><circle cx="6.5" cy="6.5" r="6" fill="none" stroke="#555"/><path d="M9 6.5H4M6 4.5l-2 2 2 2" stroke="#555" fill="none"/></svg>
    <svg width="13" height="13" viewBox="0 0 13 13"><circle cx="6.5" cy="6.5" r="6" fill="none" stroke="#555"/><path d="M4 6.5h5M7 4.5l2 2-2 2" stroke="#555" fill="none"/></svg>
  </div>
</section>

<footer class="abs footer">
  <h3 style="left:196px">Quick Links</h3>
  <ul class="links" style="left:207px"><li>HOME</li><li>ABOUT US</li><li>WHAT WE DO</li><li>NEWS BLOG</li></ul>
  <ul class="links" style="left:292px"><li>ARTICLES</li><li>CLIENTS</li><li>PARTNERS</li><li>CONTACT US</li></ul>
  <span class="fdiv" style="left:385px"></span>
  <h3 style="left:426px">Newsletter Signup</h3>
  <p class="news-sign">Lorem ipsum dolor sit amet, consectetuer adipiscing elit.</p>
  <div class="email-field">Enter your email address</div>
  <div class="submit">SUBMIT</div>
  <span class="fdiv" style="left:589px"></span>
  <h3 style="left:630px">Contact Info</h3>
  <div class="map" role="img" aria-label="Street map showing office location"></div>
  <svg class="contact-ico" style="top:50px" width="9" height="12" viewBox="0 0 9 12"><path d="M4.5 12S0 6.5 0 4.5a4.5 4.5 0 019 0C9 6.5 4.5 12 4.5 12z" fill="var(--gold)"/><circle cx="4.5" cy="4.5" r="1.6" fill="var(--plum)"/></svg>
  <p class="contact" style="top:50px;width:100px">Lorem ipsum dolor sit amet, consectetuer adipiscing elit.</p>
  <svg class="contact-ico" style="top:90px" width="10" height="10" viewBox="0 0 10 10"><circle cx="5" cy="5" r="4.3" fill="none" stroke="var(--gold)" stroke-width="1.2"/><path d="M3.5 3c0 2 1.5 3.5 3.5 3.5" stroke="var(--gold)" stroke-width="1.5" fill="none"/></svg>
  <p class="contact" style="top:89px">020 7000 4812</p>
  <svg class="contact-ico" style="top:109px" width="11" height="8" viewBox="0 0 11 8"><rect width="11" height="8" fill="var(--gold)"/><path d="M0 0l5.5 4.5L11 0" stroke="var(--plum)" fill="none"/></svg>
  <p class="contact" style="top:107px">website@plumbwick.net</p>
</footer>

<div class="abs copy-bar"></div>
<div class="abs copy">© 2014 plumbwick. All Rights Reserved.</div>
<span class="social" style="left:736px"></span>
<span class="social" style="left:762px"></span>
<span class="social" style="left:788px"></span>
<span class="social" style="left:815px"></span>
</body>
</html>
```